Modern stationary/business card design for KMR Interior Solutions
KMR Interior Solutions
Modern
Tobias Wrenfield
VP
8126 B Larchvale
Brookfield, TX 77594
tobias@stonecrestworks.com
www.stonecrestworks.com
We are open to tag lines so feel free to explore. I will give feedback to point you in the right direction.
Possibly a list of all the services we provide...
Granite, Quartz, Tile, Vinyl, Wood, Carpet, Mirrors, Cabinets, Hardware
I have more colors to choose from.

```html
<!DOCTYPE html>
<html lang="en">
<head>
<meta charset="utf-8">
<title>KMR Interior Solutions – Business Card</title>
<link href="https://fonts.googleapis.com/css2?family=Open+Sans:wght@300;400;600;700&display=swap" rel="stylesheet">
<style>
  :root {
    --olive: #b2ab55;
    --olive-dark: #9c9545;
    --paper: #ffffff;
    --ink: #6f6f6f;
    --rule: #c9c9c9;
    --stripe: #a9a9a9;
    --backdrop: #ebe8e3;
  }
  * { margin: 0; padding: 0; box-sizing: border-box; }
  html, body { width: 1200px; height: 989px; overflow: hidden; }
  body {
    background: var(--backdrop);
    font-family: "Open Sans", Arial, sans-serif;
    position: relative;
  }
  .card {
    position: absolute;
    width: 720px;
    height: 412px;
    box-shadow: 0 6px 18px rgba(0,0,0,0.18);
    overflow: hidden;
  }
  /* back side */
  .card-back { left: 380px; top: 50px; background: var(--olive); }
  .card-back .brand-mark {
    position: absolute; left: 0; right: 0; top: 130px;
    display: flex; justify-content: center; align-items: center; gap: 16px;
    color: var(--paper); font-weight: 600; font-size: 64px; letter-spacing: 4px;
  }
  .card-back .brand-mark .square { width: 26px; height: 26px; background: var(--paper); }
  .card-back .web-back {
    position: absolute; left: 0; right: 0; bottom: 34px; text-align: center;
    color: var(--paper); font-size: 20px; font-weight: 600; letter-spacing: 6px;
  }
  /* front side */
  .card-front { left: 100px; top: 500px; background: var(--paper); }
  .brand {
    position: absolute; left: 40px; top: 70px; width: 220px;
    color: var(--olive); text-align: center;
  }
  .brand .square { display: block; width: 54px; height: 54px; background: var(--olive); margin: 0 auto 12px; }
  .brand .initials { display: block; font-size: 56px; font-weight: 400; line-height: 1; letter-spacing: 2px; }
  .brand .descriptor { display: block; font-size: 19px; font-weight: 400; margin-top: 4px; white-space: nowrap; }
  .divider {
    position: absolute; left: 280px; top: 56px; width: 1px; height: 236px; background: var(--rule);
  }
  .contact { position: absolute; left: 304px; top: 56px; color: var(--ink); }
  .contact .name { color: var(--olive); font-size: 20px; font-weight: 600; }
  .contact .role { font-size: 14px; margin-bottom: 14px; }
  .contact ul { list-style: none; }
  .contact li { display: flex; align-items: center; gap: 9px; font-size: 13.5px; height: 25px; white-space: nowrap; }
  .contact li.indent { padding-left: 27px; }
  .contact svg { width: 18px; height: 18px; flex: none; }
  .band {
    position: absolute; left: 0; right: 0; bottom: 26px; height: 46px; background: var(--olive);
    color: var(--paper); text-align: center; line-height: 46px;
    font-size: 17px; font-weight: 600; letter-spacing: 6px;
  }
  .stripe { position: absolute; left: 0; right: 0; bottom: 14px; height: 8px; background: var(--stripe); }
  .base { position: absolute; left: 0; right: 0; bottom: 0; height: 14px; background: var(--olive-dark); }
</style>
</head>
<body>

<section class="card card-back">
  <div class="brand-mark"><span class="square"></span>KMR</div>
  <div class="web-back">www.StonecrestWorks.com</div>
</section>

<section class="card card-front">
  <div class="brand">
    <span class="square"></span>
    <span class="initials">KMR</span>
    <span class="descriptor">Interior Solutions</span>
  </div>
  <div class="divider"></div>

  <div class="contact">
    <p class="name">Tobias Wrenfield</p>
    <p class="role">VP</p>
    <ul>
      <li>
        <svg viewBox="0 0 18 18"><circle cx="9" cy="9" r="9" fill="var(--olive)"/><path d="M9 4a3 3 0 0 0-3 3c0 2.3 3 6 3 6s3-3.7 3-6a3 3 0 0 0-3-3z" fill="#fff"/><circle cx="9" cy="7" r="1.1" fill="var(--olive)"/></svg>
        8126 B Larchvale
      </li>
      <li class="indent">Brookfield, TX 77594</li>
      <li>
        <svg viewBox="0 0 18 18"><circle cx="9" cy="9" r="9" fill="var(--olive)"/><path d="M6 4.5l1.8 2.2-1 1.2a6 6 0 0 0 3.3 3.3l1.2-1 2.2 1.8-1.2 1.5C8.6 13.4 4.6 9.4 4.5 5.7z" fill="#fff"/></svg>
        713-555-0142
      </li>
      <li>
        <svg viewBox="0 0 18 18"><circle cx="9" cy="9" r="9" fill="var(--olive)"/><rect x="6.5" y="4" width="5" height="10" rx="1" fill="#fff"/><rect x="7.3" y="5.2" width="3.4" height="6" fill="var(--olive)"/></svg>
        832-555-0187
      </li>
      <li>
        <svg viewBox="0 0 18 18"><circle cx="9" cy="9" r="9" fill="var(--olive)"/><rect x="5" y="7.5" width="8" height="5" rx="0.8" fill="#fff"/><rect x="6.5" y="4.5" width="5" height="3" fill="#fff"/></svg>
        713-555-0169
      </li>
      <li>
        <svg viewBox="0 0 18 18"><circle cx="9" cy="9" r="9" fill="var(--olive)"/><rect x="4.5" y="5.5" width="9" height="7" fill="#fff"/><path d="M4.5 5.5L9 9.5l4.5-4" stroke="var(--olive)" stroke-width="1" fill="none"/></svg>
        tobias@stonecrestworks.com
      </li>
      <li>
        <svg viewBox="0 0 18 18"><circle cx="9" cy="9" r="9" fill="var(--olive)"/><circle cx="9" cy="9" r="4.5" fill="none" stroke="#fff" stroke-width="1.2"/><path d="M4.5 9h9M9 4.5c-2 2.5-2 6.5 0 9M9 4.5c2 2.5 2 6.5 0 9" stroke="#fff" stroke-width="1" fill="none"/></svg>
        www.stonecrestworks.com
      </li>
    </ul>
  </div>

  <div class="band">www.StonecrestWorks.com</div>
  <div class="stripe"></div>
  <div class="base"></div>
</section>

</body>
</html>
```